Cannabis & Shroom Informative

Online Blog/Informative website design
Example site: https://leafharborshop.com/

I will need the Ad space as well.

Target Market(s)

Cannabis and (psyho) Mushroom Users

Number of Pages Required

1 page

Colors

Designer to choose colors to be used in the design.

```html
<!DOCTYPE html>
<html lang="en">
<head>
<meta charset="utf-8">
<title>Canopy Ledger</title>
<link href="https://fonts.googleapis.com/css2?family=Roboto:wght@400;500;700&family=Signika:wght@600;700&display=swap" rel="stylesheet">
<style>
:root{
  --teal:#15a386;--lime:#8cc63f;--forest:#3d5a4a;--ink:#2b2b2b;--muted:#8a8a8a;
  --soft:#f6f7f6;--footer:#1d3327;--line:#e6e6e6;
}
*{box-sizing:border-box;margin:0;padding:0}
html,body{width:1200px;height:3798px;overflow:hidden;background:#fff;font-family:'Roboto',sans-serif;color:var(--ink)}
.page{position:relative;width:1200px;height:3798px}
.abs{position:absolute}
.topbar{left:0;top:0;width:1200px;height:40px;background:var(--teal);color:#fff;font-size:13px}
.topbar .mail{left:143px;top:12px}
.dots{right:143px;top:13px;display:flex;gap:9px}
.dots span{width:14px;height:14px;border-radius:50%;background:#fff}
.brand{display:flex;align-items:center;gap:10px;font-family:'Signika',sans-serif;font-weight:700;font-size:29px;color:var(--lime)}
.brand i{width:22px;height:22px;border-radius:50%;background:var(--teal);display:block}
.header .brand{position:absolute;left:143px;top:74px}
.ad{left:681px;top:56px;width:375px;height:63px;background:linear-gradient(90deg,#8cc63f 0 36%,#56724a 60%,#9aa17a);display:flex;align-items:center;padding-left:14px;gap:16px;color:#fff;font-family:'Signika',sans-serif;font-weight:700}
.ad .lp{font-size:17px;line-height:19px}
.ad .off{width:44px;height:44px;border-radius:50%;background:var(--teal);font-size:14px;line-height:15px;text-align:center;padding-top:7px}
.nav{left:0;top:136px;width:1200px;height:57px;background:#f5f5f5;display:flex;padding-left:143px}
.nav a{font-size:14px;font-weight:500;color:#333;text-decoration:none;line-height:57px;padding:0 18px}
.nav a.on{background:var(--teal);color:#fff;padding:0 14px}
.hero{left:0;top:193px;width:1200px;height:475px;background:linear-gradient(110deg,#6b4a2c,#a07a4f 35%,#7d5a36 60%,#4f3a25)}
.hero h1{position:absolute;left:634px;top:90px;font-family:'Signika',sans-serif;font-weight:700;font-size:66px;line-height:70px;color:#fff}
.btn{display:inline-block;border-radius:25px;color:#fff;font-weight:500;font-size:14px;text-align:center}
.hero .btn{position:absolute;left:634px;top:251px;width:162px;height:47px;line-height:47px;background:var(--teal)}
.arrow{width:44px;height:44px;border-radius:50%;background:#333;top:177px}
.arrow svg{display:block;margin:14px}
.deals{left:143px;top:563px;width:913px;height:261px;display:flex}
.deal{flex:1;padding:12px 12px 0;color:#fff;text-align:center;font-weight:700;font-size:18px}
.deal .ph{height:196px}
.deal p{line-height:52px}
.welcome-art{left:140px;top:870px;width:332px;height:310px;background:linear-gradient(135deg,#cfe6c4,#5e9a76 55%,#9cc9c2)}
.welcome{left:560px;top:910px;width:496px}
.welcome h2{font-family:'Signika',sans-serif;font-weight:700;font-size:40px;line-height:46px}
.welcome h2 span{color:var(--lime)}
.welcome p{margin-top:28px;font-size:13px;line-height:27px;color:var(--muted)}
.blog{left:0;top:1260px;width:1200px;height:1072px;background:var(--soft)}
.sec-title{position:absolute;left:0;width:1200px;text-align:center;font-family:'Signika',sans-serif;font-weight:700;font-size:38px}
.sec-title span{color:var(--lime)}
.card{position:absolute;width:283px;height:380px;background:#fff;border:1px solid var(--line)}
.card .ph{height:187px}
.card .txt{height:191px;padding:24px 24px 0}
.card h3{font-size:16px;font-weight:500}
.card p{margin-top:14px;font-size:12px;line-height:21px;color:var(--muted)}
.meta{margin-top:14px;display:flex;align-items:center;font-size:12px;color:#555;gap:6px}
.meta b{width:8px;height:8px;border-radius:50%;background:var(--lime)}
.meta .sq{margin-left:auto;display:flex;gap:4px}
.meta .sq i{width:20px;height:20px;border-radius:50%;display:block}
.disp{position:absolute;width:283px;height:212px;background:#fff;box-shadow:0 2px 10px rgba(0,0,0,.08);text-align:center}
.disp .name{display:flex;align-items:center;justify-content:center;gap:8px;height:128px;padding-top:20px;font-size:24px;font-weight:700;color:var(--forest)}
.disp .name i{width:16px;height:16px;border-radius:50%;background:var(--teal);display:block}
.disp .btn{width:218px;height:49px;line-height:49px}
.g{background:var(--teal)}.l{background:var(--lime)}.d{background:var(--forest)}
.shrooms{left:0;top:3309px;width:1200px;height:108px;background:linear-gradient(#fff,#f2dcd6 55%,#c9d7b8)}
.footer{left:0;top:3417px;width:1200px;height:335px;background:var(--footer);color:#fff}
.footer .brand{position:absolute;left:143px;top:48px}
.footer .about{position:absolute;left:143px;top:108px;width:360px;font-size:13px;line-height:22px}
.footer .soc{position:absolute;left:143px;top:240px;display:flex;gap:16px}
.footer .soc i{width:20px;height:20px;border-radius:50%;background:#fff;display:block}
.footer h4{font-size:20px;font-weight:500}
.links{position:absolute;left:585px;top:60px}
.links ul{list-style:none;margin-top:18px;font-size:13px;line-height:27px}
.news{position:absolute;left:802px;top:60px;width:254px}
.news p{margin-top:18px;font-size:13px}
.news .in{margin-top:20px;height:38px;background:#fff;color:#666;font-size:12px;line-height:38px;padding-left:25px}
.news .sub{margin-top:10px;width:112px;height:36px;background:var(--lime);font-size:13px;font-weight:700;line-height:36px;text-align:center}
.bottom{left:0;top:3752px;width:1200px;height:46px;background:var(--teal);color:#fff;font-size:13px;text-align:center;line-height:46px}
</style>
</head>
<body>
<div class="page">
  <div class="abs topbar"><span class="abs mail">✉ hello@canopyledger.net</span><div class="abs dots"><span></span><span></span><span></span><span></span></div></div>
  <div class="header"><div class="brand"><i></i>CANOPY LEDGER</div></div>
  <div class="abs ad"><div class="lp">LOWEST<br>PRICE</div><div class="off">$10<br>OFF</div></div>
  <nav class="abs nav"><a class="on">HOME</a><a>REVIEWS</a><a>SHOP</a><a>TOP DISPENSARIES</a><a>ABOUT US</a><a>NEWS</a><a>INFORMATION</a><a>CONTACT US</a></nav>

  <section class="abs hero" role="img" aria-label="Amber dropper bottle beside a burlap sack of dried cannabis buds">
    <h1>CANOPY<br>LEDGER</h1>
    <a class="btn">GET STARTED</a>
    <div class="abs arrow" style="left:31px"><svg width="16" height="16"><path d="M11 2 5 8l6 6" fill="none" stroke="#fff" stroke-width="2"/></svg></div>
    <div class="abs arrow" style="left:1125px"><svg width="16" height="16"><path d="m5 2 6 6-6 6" fill="none" stroke="#fff" stroke-width="2"/></svg></div>
  </section>

  <div class="abs deals">
    <div class="deal l"><div class="ph" role="img" aria-label="Glass jars of concentrates" style="background:linear-gradient(135deg,#3a3a30,#8a8f78)"></div><p>CONCENTRATE DEALS</p></div>
    <div class="deal g" style="background:#6cc0b6"><div class="ph" role="img" aria-label="Jar of spilled cannabis buds" style="background:linear-gradient(135deg,#9aa46a,#5d6a3c)"></div><p>CANNABIS DEALS</p></div>
    <div class="deal l"><div class="ph" role="img" aria-label="Bowl of ground herb and a rolled cone" style="background:linear-gradient(135deg,#1e3b3e,#3f6d55 60%,#d8dccd)"></div><p>COUPON CODES</p></div>
  </div>

  <div class="abs welcome-art" role="img" aria-label="Leaf shape filled with forest imagery"></div>
  <div class="abs welcome">
    <h2>WELCOME TO<br><span>CANOPY LEDGER</span></h2>
    <p>Lorem ipsum dolor sit amet, consectetur adipiscing elit, sed do eiusmod tempor incididunt ut labore et dolore magna aliqua. Quis ipsum suspendisse ultrices gravida. Risus commodo viverra Lorem ipsum dolor sit amonsectetur adipiscing elit do eiusmod tempor incididunt ut labore et dolore magna aliquis ipsum suspendisse ultrices grisus commodo viverra maecenas</p>
  </div>

  <section class="abs blog">
    <h2 class="sec-title" style="top:92px">BLOG <span>POSTS</span></h2>
  </section>
  <!-- row 1 -->
  <article class="card" style="left:143px;top:1437px"><div class="ph" role="img" aria-label="Mushroom soup with fresh mushrooms" style="background:linear-gradient(135deg,#5a3e2a,#c9b49a)"></div><div class="txt"><h3>DUCIMUS QUI BLANDITIIS</h3><p>Lorem ipsum dolor sit aconsectetur adipiscing elit, sed do eiusmod empor aliquasum suspendissetrices.</p><div class="meta"><b></b>Comments | Likes<span class="sq"><i class="d"></i><i class="g"></i><i class="d"></i></span></div></div></article>
  <article class="card" style="left:458px;top:1437px"><div class="txt"><h3>DUCIMUS QUI BLANDITIIS</h3><p>Lorem ipsum dolor sit aconsectetur adipiscing elit, sed do eiusmod empor aliquasum suspendissetrices.</p><div class="meta"><b></b>Comments | Likes<span class="sq"><i class="d"></i><i class="g"></i><i class="d"></i></span></div></div><div class="ph" role="img" aria-label="Hands rolling ground herb in paper" style="background:linear-gradient(135deg,#2a2a2a,#c9b39e 60%,#3a3a3a)"></div></article>
  <article class="card" style="left:774px;top:1437px"><div class="ph" role="img" aria-label="Cannabis flower close-up on dark background" style="background:radial-gradient(circle at 50% 60%,#c2c58c,#1a2430 65%)"></div><div class="txt"><h3>DUCIMUS QUI BLANDITIIS</h3><p>Lorem ipsum dolor sit aconsectetur adipiscing elit, sed do eiusmod empor aliquasum suspendissetrices.</p><div class="meta"><b></b>Comments | Likes<span class="sq"><i class="d"></i><i class="g"></i><i class="d"></i></span></div></div></article>
  <!-- row 2 -->
  <article class="card" style="left:143px;top:1848px"><div class="txt"><h3>DUCIMUS QUI BLANDITIIS</h3><p>Lorem ipsum dolor sit aconsectetur adipiscing elit, sed do eiusmod empor aliquasum suspendissetrices.</p><div class="meta"><b></b>Comments | Likes<span class="sq"><i class="d"></i><i class="g"></i><i class="d"></i></span></div></div><div class="ph" role="img" aria-label="Spilled jar of buds beside a rolled joint" style="background:linear-gradient(135deg,#6b6a5a,#a8a77a 50%,#8d5e3a)"></div></article>
  <article class="card" style="left:458px;top:1848px"><div class="ph" role="img" aria-label="Gloved hand trimming a cannabis plant" style="background:linear-gradient(135deg,#3c4a3a,#8ca065 55%,#2c3a2c)"></div><div class="txt"><h3>DUCIMUS QUI BLANDITIIS</h3><p>Lorem ipsum dolor sit aconsectetur adipiscing elit, sed do eiusmod empor aliquasum suspendissetrices.</p><div class="meta"><b></b>Comments | Likes<span class="sq"><i class="d"></i><i class="g"></i><i class="d"></i></span></div></div></article>
  <article class="card" style="left:774px;top:1848px"><div class="txt"><h3>DUCIMUS QUI BLANDITIIS</h3><p>Lorem ipsum dolor sit aconsectetur adipiscing elit, sed do eiusmod empor aliquasum suspendissetrices.</p><div class="meta"><b></b>Comments | Likes<span class="sq"><i class="d"></i><i class="g"></i><i class="d"></i></span></div></div><div class="ph" role="img" aria-label="Basket of fresh mushrooms" style="background:linear-gradient(135deg,#3a2a1c,#d8c8b0 55%,#5a3e26)"></div></article>

  <h2 class="sec-title" style="top:2430px">OUR <span>TOP DISPENSARIES</span></h2>
  <div class="disp" style="left:143px;top:2538px"><div class="name"><i></i>Greenrow</div><a class="btn d">READ THE REVIEW HERE</a></div>
  <div class="disp" style="left:458px;top:2538px"><div class="name"><i></i>Petalbay</div><a class="btn g">READ THE REVIEW HERE</a></div>
  <div class="disp" style="left:774px;top:2538px"><div class="name"><i></i>Stem &amp; Sprout</div><a class="btn l">READ THE REVIEW HERE</a></div>
  <div class="disp" style="left:143px;top:2783px"><div class="name"><i></i>Oilhaven</div><a class="btn g">READ THE REVIEW HERE</a></div>
  <div class="disp" style="left:458px;top:2783px"><div class="name"><i></i>Fieldmark</div><a class="btn l">READ THE REVIEW HERE</a></div>
  <div class="disp" style="left:774px;top:2783px"><div class="name"><i></i>Northglen</div><a class="btn d">READ THE REVIEW HERE</a></div>
  <div class="disp" style="left:143px;top:3026px"><div class="name"><i></i>Tendril Care</div><a class="btn l">READ THE REVIEW HERE</a></div>
  <div class="disp" style="left:458px;top:3026px"><div class="name"><i></i>Budline</div><a class="btn g">READ THE REVIEW HERE</a></div>
  <div class="disp" style="left:774px;top:3026px"><div class="name"><i></i>Mossworks</div><a class="btn d">READ THE REVIEW HERE</a></div>

  <div class="abs shrooms" role="img" aria-label="Faint row of red-capped mushrooms on grass"></div>

  <footer class="abs footer">
    <div class="brand"><i></i>CANOPY LEDGER</div>
    <p class="about">Lorem ipsum dolor sit amet, consectetur adipiscing elit, sed do eiusmod tempor incididunt ut labore et dolore magiquauis ipsum suspendisse ultrices gravidasus commodo viverra maecenas accumsan lacus vel facilisis.</p>
    <div class="soc"><i></i><i></i><i></i><i></i></div>
    <div class="links"><h4>Quick Links</h4><ul><li>Home</li><li>Services</li><li>About Us</li><li>Reviews</li><li>Contact</li><li>Information</li></ul></div>
    <div class="news"><h4>Sign Up Newsletter</h4><p>At vero eos et accusamus et iusto odio</p><div class="in">Enter Email</div><div class="sub">SUBSCRIBE</div></div>
  </footer>
  <div class="abs bottom">© 2020 Canopy Ledger.All rights reserved &nbsp;|&nbsp; Privacy Policy</div>
</div>
</body>
</html>
```